Brochure/Catalog for Door Manufacturer and Designer

Harlow Door Design is a door manufacturer and distributor based out of the Southwest United States. We need a catalog showcasing our four door collections.
We have a clear vision on what the catalog will look like (SEE INSTRUCTIONS ATTACHED), but we need a creative designer to put it all together.
We have attached:
- Catalog instructions (brochure.doc)
- Our logo (GHN094.png)
- A zip folder with Images (images.zip)
Please read the attached brochure instructions and contact us with any questions.
Thank you for your time and we look forward to seeing your design!
Harlow Door Design
Distributor

```html
<!DOCTYPE html>
<html lang="en">
<head>
<meta charset="utf-8">
<title>Harlow Door Design — Welcome</title>
<link rel="stylesheet" href="https://fonts.googleapis.com/css2?family=Dancing+Script:wght@400;500&family=Pinyon+Script&display=swap">
<style>
  :root {
    --paper: #ded8c3;
    --ink: #1d1a17;
    --navy: #1b2a55;
    --rule-brown: #a06d55;
    --accent-red: #9b1c1c;
    --rule-dark: #3a3632;
    --marker-red: #b3262a;
  }
  * { margin: 0; padding: 0; box-sizing: border-box; }
  html, body { width: 927px; height: 1200px; overflow: hidden; background: var(--paper); }
  .page {
    position: relative;
    width: 927px;
    height: 1200px;
    background: var(--paper);
    color: var(--ink);
    font-family: "Dancing Script", cursive;
  }
  .ornament {
    position: absolute;
    left: 152px;
    top: 110px;
    width: 640px;
    height: 146px;
    background: radial-gradient(ellipse at 50% 60%, var(--navy) 0%, #2a3a68 55%, rgba(27,42,85,0.55) 100%);
    border-radius: 50% 50% 6px 6px / 80% 80% 6px 6px;
    opacity: 0.85;
  }
  .header-rule {
    position: absolute;
    left: 110px;
    top: 254px;
    width: 724px;
    height: 14px;
  }
  .intro {
    position: absolute;
    top: 325px;
    left: 0;
    width: 927px;
    text-align: center;
    font-size: 22px;
  }
  .intro .drop-cap {
    font-family: "Pinyon Script", cursive;
    font-size: 62px;
    line-height: 1;
    vertical-align: -6px;
  }
  .copy {
    position: absolute;
    top: 434px;
    left: 100px;
    width: 727px;
    text-align: center;
    font-size: 23px;
    line-height: 41px;
  }
  .copy p { margin-bottom: 16px; }
  .copy .call-to-action {
    color: var(--accent-red);
    font-size: 30px;
    font-weight: 500;
    margin-top: 4px;
  }
  .footer-rule {
    position: absolute;
    left: 108px;
    top: 1003px;
    width: 712px;
    height: 1px;
    background: var(--rule-dark);
  }
  .page-marker {
    position: absolute;
    left: 815px;
    top: 1088px;
    width: 80px;
    height: 82px;
  }
</style>
</head>
<body>
<main class="page">
  <div class="ornament" role="img" aria-label="Navy scrollwork ornament with a central lotus flourish"></div>
  <svg class="header-rule" viewBox="0 0 724 14" aria-hidden="true">
    <line x1="0" y1="7" x2="724" y2="7" stroke="var(--rule-brown)" stroke-width="2"/>
    <polygon points="362,1 371,7 362,13 353,7" fill="var(--rule-brown)"/>
  </svg>

  <p class="intro"><span class="drop-cap">F</span>or over fifteen years,</p>

  <section class="copy">
    <p>Our master craftsmen and builders have been providing high quality doors throughout the Southwestern United States and Mexico.</p>
    <p>Our team of designer's loves what they do. That's what separates Harlow Door Design with the competition –this isn't just a job, this is a passion. As such, we take each client seriously and we work patiently, side by side, to get your design just right. Life is all about first impressions, and a custom quality door from Harlow Door Design is sure to leave a positive and lasting impression.</p>
    <p>Because quality is of our utmost concern, we only use the most premium wood and each door is manufactured under the strictest manufacturing standards and quality control.</p>
    <p>We encourage you to look through our collections and reach out to us.</p>
    <p class="call-to-action">Allow us to help design your new door!</p>
  </section>

  <div class="footer-rule"></div>

  <svg class="page-marker" viewBox="0 0 80 82" aria-label="Page 2">
    <polygon points="2,26 28,2 74,50 76,78 48,76" fill="none" stroke="var(--marker-red)" stroke-width="1.5"/>
    <text x="42" y="48" font-family="Arial, sans-serif" font-size="12" fill="var(--ink)" text-anchor="middle">2</text>
  </svg>
</main>
</body>
</html>
```